Redesign of business card for Cedar Ridge Mechanical

We are looking for a new design for our business cards for Cedar Ridge Mechanical. We are a plumbing & HVAC construction company, operating on the West Coast of Canada and USA. Logo attached.
Industry/Entity Type
Construction - Plumbing & HVAC
Contact Information for Business Card
Name, address, phone numbers, email, website address
Look and feel
Each slider illustrates characteristics of the customer's brand and the style your logo design should communicate.

```html
<!DOCTYPE html>
<html lang="en">
<head>
<meta charset="utf-8">
<title>Cedar Ridge Mechanical – Business Card</title>
<link rel="stylesheet" href="https://fonts.googleapis.com/css2?family=Montserrat:wght@400;500;700&display=swap">
<style>
  :root {
    --page-bg: #1f1f1f;
    --card-front: #ffffff;
    --card-back: #1a1a1a;
    --card-back-edge: #2c2c2c;
    --ink: #161616;
    --ink-soft: #2a2a2a;
    --back-mark: #3a3a3a;
  }
  * { margin: 0; padding: 0; box-sizing: border-box; }
  html, body {
    width: 1200px; height: 1200px; overflow: hidden;
    background: var(--page-bg);
    font-family: "Montserrat", Arial, sans-serif;
  }
  .canvas { position: relative; width: 1200px; height: 1200px; }
  .card {
    position: absolute; left: 232px; width: 682px; height: 408px;
    border-radius: 24px;
  }
  .card--front { top: 217px; background: var(--card-front); color: var(--ink); }
  .card--back {
    top: 696px; height: 402px; background: var(--card-back);
    border: 1px solid var(--card-back-edge);
    display: flex; align-items: center; justify-content: center;
  }
  .person { position: absolute; left: 32px; top: 44px; }
  .person__name { font-weight: 700; font-size: 25px; line-height: 1.1; }
  .person__title { font-weight: 400; font-size: 15px; margin-top: 5px; color: var(--ink-soft); }
  .brand {
    position: absolute; right: 49px; top: 52px;
    display: flex; align-items: center; gap: 10px;
    font-weight: 700; font-size: 17px; letter-spacing: 0.3px; color: var(--ink);
  }
  .brand__square { width: 14px; height: 14px; background: var(--ink); }
  .contacts { position: absolute; left: 32px; top: 280px; list-style: none; }
  .contacts__item {
    display: flex; align-items: center; gap: 11px;
    font-size: 15px; height: 28.5px; color: var(--ink);
  }
  .contacts__icon { width: 14px; height: 14px; flex: none; }
  .address {
    position: absolute; right: 49px; top: 322px; text-align: right;
    font-size: 15px; line-height: 21px; color: var(--ink);
  }
  .back-brand {
    display: flex; align-items: center; gap: 18px;
    font-weight: 700; font-size: 36px; letter-spacing: 0.5px; color: var(--back-mark);
  }
  .back-brand__square { width: 26px; height: 26px; background: var(--back-mark); }
</style>
</head>
<body>
<main class="canvas">
  <section class="card card--front" aria-label="Card front">
    <div class="person">
      <p class="person__name">Daniel Harper</p>
      <p class="person__title">Managing Director</p>
    </div>
    <div class="brand">
      <span class="brand__square"></span>
      <span class="brand__name">Cedar Ridge Mechanical</span>
    </div>
    <ul class="contacts">
      <li class="contacts__item">
        <svg class="contacts__icon" viewBox="0 0 24 24"><path fill="currentColor" d="M6.6 10.8a15.1 15.1 0 0 0 6.6 6.6l2.2-2.2c.3-.3.7-.4 1-.2 1.1.4 2.3.6 3.6.6.6 0 1 .4 1 1V20c0 .6-.4 1-1 1A17 17 0 0 1 3 4c0-.6.4-1 1-1h3.5c.6 0 1 .4 1 1 0 1.3.2 2.5.6 3.6.1.3 0 .7-.2 1z"/></svg>
        <span>555.204.7160</span>
      </li>
      <li class="contacts__item">
        <svg class="contacts__icon" viewBox="0 0 24 24"><path fill="currentColor" d="M2 5h20v14H2z"/><path fill="none" stroke="#fff" stroke-width="2" d="M2 6l10 7 10-7"/></svg>
        <span>info@cedarridgemechanical.com</span>
      </li>
      <li class="contacts__item">
        <svg class="contacts__icon" viewBox="0 0 24 24"><circle cx="12" cy="12" r="10" fill="currentColor"/><path fill="none" stroke="#fff" stroke-width="1.5" d="M2 12h20M12 2c3 3 3 17 0 20M12 2c-3 3-3 17 0 20"/></svg>
        <span>www.cedarridgemechanical.com</span>
      </li>
    </ul>
    <address class="address" style="font-style:normal">
      48 Alder Creek Road<br>Tacoma, WA 98402
    </address>
  </section>

  <section class="card card--back" aria-label="Card back">
    <div class="back-brand">
      <span class="back-brand__square"></span>
      <span class="back-brand__name">Cedar Ridge Mechanical</span>
    </div>
  </section>
</main>
</body>
</html>
```